Keepsakes of Mine trifold brochure design

We are a start up company that will help seniors write their memoirs...beginning with a few ancestors and their heritage and continuing through their own history...how they would like to be remembered in the next generation. I envision a senior citizen at an older writing desk, writing her memoirs, with a book (maybe standing on top, leaning slightly) that has the words Keepsakes of Mine.com on the back binding. OR maybe a senior couple walking into the sunset with the same book somewhere in the frame. Communicating the relevance of every life being significant to those that come after them...when a genealogy doesn't say enough about the details of one's life. Please note that I am open to the professionals own ideas...I am not locked into my concepts. I would like one or two phrases..."When A Genealogy Doesn't Say Enough" and/or "Every life legacy is a gift for the next generation to treasure" to be in the design.
A few documents are loaded that contain notes for our web designers. Maybe they will help you with our thoughts.
Updates

Reason: We have added some additional photos that might be useful.

Target Market(s)

Seniors and the baby boomer generation

Industry/Entity Type

Graphic Design

Requirements
Must have
• Keepsakes of Mine
• Doris Whitcombe, M.A.
• 1-555-218-6470 (local)
• 1-855-7RELICS (toll free)
• info@keepsakesofmine.example
• keepsakesofmine.example
Should not have
• Scripts that would be challenging for seniors to read.

```html
<!DOCTYPE html>
<html lang="en">
<head>
<meta charset="utf-8">
<title>Keepsakes of Mine – Trifold Brochure</title>
<link rel="stylesheet" href="https://fonts.googleapis.com/css2?family=Lora:ital,wght@0,400;0,500;1,400;1,500&display=swap">
<style>
  :root {
    --ink: #2b1d17;
    --cream: #f3e6c4;
    --gold: #e6cf8a;
    --butter: #fae4a3;
    --lilac: #d7aad5;
    --lilac-text: #d9b6d6;
    --plum-dark: #2d1f22;
    --espresso: #2a1a14;
    --line-purple: #b58fc0;
    --line-yellow: #f1d98c;
  }
  * { margin: 0; padding: 0; box-sizing: border-box; }
  html, body { width: 1200px; height: 849px; overflow: hidden; background: #fff; }
  body { font-family: "Lora", Georgia, serif; }

  .brochure { position: relative; width: 1200px; height: 849px; display: flex; }
  .panel { position: relative; width: 400px; height: 849px; overflow: hidden; }

  /* Left panel */
  .photo-bench {
    position: absolute; left: 0; top: 0; width: 400px; height: 383px;
    background: linear-gradient(160deg, #6b5a55 0%, #8a5a52 30%, #b9a79a 55%, #6d4a3f 80%, #3f2c26 100%);
  }
  .headline {
    position: absolute; left: 36px; top: 40px;
    font-size: 31px; line-height: 34px; font-weight: 500;
    letter-spacing: 1px;
    color: var(--cream);
  }
  .rule-purple { position: absolute; left: 0; top: 383px; width: 400px; height: 4px; background: var(--line-purple); }
  .invite {
    position: absolute; left: 0; top: 387px; width: 400px; height: 214px;
    background: var(--plum-dark);
    color: var(--lilac-text);
    text-align: center;
    font-size: 18px; line-height: 22px; letter-spacing: 1px;
    padding-top: 18px;
  }
  .invite p + p { margin-top: 22px; }
  .rule-yellow { position: absolute; left: 0; top: 601px; width: 400px; height: 3px; background: var(--line-yellow); }
  .photo-reading {
    position: absolute; left: 0; top: 604px; width: 400px; height: 245px;
    background: linear-gradient(135deg, #ece4d8 0%, #d9c9b4 40%, #b08a6a 70%, #6e5645 100%);
  }

  /* Middle panel */
  .panel-story { background: var(--butter); }
  .story {
    position: absolute; left: 29px; top: 26px; width: 365px;
    font-style: italic; font-size: 17.2px; line-height: 20px; letter-spacing: 0.55px;
    color: var(--ink);
  }
  .story p + p { margin-top: 20px; }
  .contact {
    position: absolute; left: 0; top: 677px; width: 400px; height: 152px;
    background: var(--lilac);
    padding: 12px 0 0 46px;
    font-style: normal;
    font-size: 18px; line-height: 22px; color: var(--ink);
  }
  .contact-row { display: flex; align-items: flex-start; }
  .contact-row + .contact-row { margin-top: 13px; }
  .contact-row svg { width: 22px; height: 22px; margin-right: 12px; flex: none; }

  /* Right panel */
  .photo-desk {
    position: absolute; left: 0; top: 0; width: 400px; height: 849px;
    background:
      radial-gradient(ellipse at 30% 48%, #b97b3c 0%, rgba(120,70,35,0.6) 18%, rgba(0,0,0,0) 42%),
      radial-gradient(ellipse at 82% 40%, #d8cfc4 0%, rgba(150,130,115,0.5) 20%, rgba(0,0,0,0) 40%),
      linear-gradient(180deg, #4a2f22 0%, #5a3a28 40%, #3a2419 70%, var(--espresso) 100%);
  }
  .brand-mark {
    position: absolute; left: 0; top: 672px; width: 400px;
    text-align: center;
    font-size: 29px; font-weight: 400; letter-spacing: 0.5px; color: var(--gold);
  }
  .author {
    position: absolute; left: 0; top: 720px; width: 400px;
    text-align: center;
    font-size: 17px; letter-spacing: 0.8px; color: var(--gold);
  }
  .tagline {
    position: absolute; left: 0; top: 777px; width: 400px;
    text-align: center;
    font-style: italic; font-size: 18px; letter-spacing: 0.9px; color: var(--gold);
  }
</style>
</head>
<body>
<main class="brochure">

  <section class="panel panel-intro">
    <div class="photo-bench" role="img" aria-label="Open book resting on a red park bench"></div>
    <h1 class="headline">Ordinary<br>Lives............<br>Extraordinary<br>Legacies</h1>
    <div class="rule-purple"></div>
    <div class="invite">
      <p>If you were alive in 100 years,<br>what would you share with your<br>descendants?</p>
      <p>Now you have a vehicle to help<br>you immortalize your thoughts<br>for the future...specifically for<br>those who will want to know!</p>
    </div>
    <div class="rule-yellow"></div>
    <div class="photo-reading" role="img" aria-label="Grandfather reading a book with a small child in a bright living room"></div>
  </section>

  <section class="panel panel-story">
    <div class="story">
      <p>We are not all presidents of<br>countries or CEO’s of fortune 500<br>companies! But “every life legacy is<br>a gift to be treasured by the next<br>generation.”</p>
      <p>Does your family host generations of<br>soldiers, doctors, farmers, scientists,<br>mechanics, entrepreneurs, writers,<br>politicians, contractors, pastors,<br>artisans, athletes, musicians, etc..?<br>Generational patterns can often<br>emerge when writing your story that<br>will interest the next generation.</p>
      <p>A genealogy, while very relevant<br>doesn’t offer the personal story of<br>the names we find. A biography can<br>place a deeper relevance on the face<br>for future descendants. Every life<br>is a legacy to pass forward and we<br>at Keepsakes of Mine believe everyone<br>should chronicle their life journey<br>in writing. This commitment allows<br>you to be remembered for who you<br>truly are as a person.</p>
      <p>Think about it....Do you know the<br>triumphs and tribulations of your<br>ancestors? Do you wish you did?<br>Well, so will those falling into your<br>personal family tree.</p>
    </div>
    <address class="contact">
      <div class="contact-row">
        <svg viewBox="0 0 24 24" aria-hidden="true"><path fill="#1d1411" d="M6.6 10.8a15.1 15.1 0 0 0 6.6 6.6l2.2-2.2a1 1 0 0 1 1-.25 11.4 11.4 0 0 0 3.6.57 1 1 0 0 1 1 1V20a1 1 0 0 1-1 1A17 17 0 0 1 3 4a1 1 0 0 1 1-1h3.5a1 1 0 0 1 1 1c0 1.25.2 2.45.57 3.57a1 1 0 0 1-.25 1z"/></svg>
        <span>1-555-218-6470 (local)<br>1-855-7RELICS (toll free)</span>
      </div>
      <div class="contact-row">
        <svg viewBox="0 0 24 24" aria-hidden="true"><rect x="2.5" y="5.5" width="19" height="13" fill="none" stroke="#1d1411" stroke-width="1.6"/><path d="M2.5 5.5l9.5 8 9.5-8" fill="none" stroke="#1d1411" stroke-width="1.6"/></svg>
        <span>info@keepsakesofmine.example</span>
      </div>
      <div class="contact-row">
        <svg viewBox="0 0 24 24" aria-hidden="true"><circle cx="12" cy="12" r="10" fill="#1d1411"/><ellipse cx="12" cy="12" rx="4.5" ry="10" fill="none" stroke="#d7aad5" stroke-width="1.3"/><path d="M2 12h20M4 7h16M4 17h16" stroke="#d7aad5" stroke-width="1.3"/></svg>
        <span>www.keepsakesofmine.example</span>
      </div>
    </address>
  </section>

  <section class="panel panel-cover">
    <div class="photo-desk" role="img" aria-label="Elderly woman writing at an antique wooden desk lit by an oil lamp"></div>
    <div class="brand-mark">Keepsakes of Mine</div>
    <p class="author">Doris Whitcombe, M.A.</p>
    <p class="tagline">When a genealogy doesn’t say enough</p>
  </section>

</main>
</body>
</html>
```